Business Card Design

We provide services doing multiple jobs in the construction industry.Please note: The company name needs to be ROCK SOLID BUILDING SERVICESAttached logo was an example of what we wanted. Can you change up the colors?

Industry/Entity Type

Construction

Contact Information for Business Card

ROCK SOLID BUILDING SERVICES5401 HUDSON BEND RDAUSTIN, TX 78734(512)243-6854ROCKSOLIDBUILDINGSERVICES@GMAIL.COM

```html
<!DOCTYPE html>
<html lang="en">
<head>
<meta charset="utf-8">
<title>Pearlwood Framing Works – Business Card</title>
<link rel="stylesheet" href="https://fonts.googleapis.com/css2?family=Exo+2:wght@600;700&family=Cabin:wght@400;500&display=swap">
<style>
  :root {
    --backdrop: #3a3a3f;
    --card: #ffffff;
    --navy: #1c1a63;
    --navy-deep: #0f0e3d;
    --ink: #0c0c14;
    --cream: #efdfae;
  }
  html, body {
    margin: 0;
    width: 1200px;
    height: 960px;
    overflow: hidden;
    background: var(--backdrop);
  }
  .card {
    position: absolute;
    left: 100px;
    top: 194px;
    width: 1000px;
    height: 572px;
    background: var(--card);
    overflow: hidden;
    box-shadow: 0 18px 40px rgba(0,0,0,.45);
  }
  .card__waves {
    position: absolute;
    inset: 0;
    width: 100%;
    height: 100%;
  }
  .company {
    position: absolute;
    right: 56px;
    top: 40px;
    text-align: right;
    color: var(--navy);
    font-family: "Exo 2", sans-serif;
    font-weight: 700;
    line-height: 1;
  }
  .company__name { font-size: 62px; letter-spacing: 1px; }
  .company__tag { font-size: 31px; font-weight: 600; margin-top: 6px; letter-spacing: 1px; }
  .brandmark {
    position: absolute;
    left: 70px;
    top: 160px;
    display: flex;
    align-items: center;
    gap: 14px;
    font-family: "Exo 2", sans-serif;
    font-weight: 700;
    font-size: 30px;
    line-height: 1.05;
    color: var(--navy);
  }
  .brandmark__square {
    width: 64px;
    height: 64px;
    background: var(--navy);
    flex: none;
  }
  .person {
    position: absolute;
    left: 80px;
    top: 300px;
    color: var(--navy);
    font-family: "Cabin", sans-serif;
  }
  .person__name { font-size: 38px; font-weight: 500; }
  .person__role { font-size: 25px; margin-top: 2px; }
  .contact {
    position: absolute;
    right: 34px;
    top: 340px;
    list-style: none;
    margin: 0;
    padding: 0;
    font-family: "Cabin", sans-serif;
    font-size: 21px;
    color: var(--cream);
    text-align: right;
  }
  .contact__item {
    display: flex;
    justify-content: flex-end;
    align-items: center;
    gap: 14px;
    height: 40px;
  }
  .contact__icon { width: 22px; height: 22px; fill: #ffffff; flex: none; }
</style>
</head>
<body>
  <div class="card">
    <svg class="card__waves" viewBox="0 0 1000 572" preserveAspectRatio="none" aria-hidden="true">
      <defs>
        <linearGradient id="navyFill" x1="0" y1="0" x2="1" y2="1">
          <stop offset="0" stop-color="#2a2880"/>
          <stop offset="1" stop-color="#0f0e3d"/>
        </linearGradient>
      </defs>
      <path d="M1000 170 C780 178 600 220 500 295 C410 362 360 470 280 572 L1000 572 Z" fill="url(#navyFill)"/>
      <path d="M960 190 C760 208 610 255 530 315 C450 378 410 472 340 572 L370 572 C440 472 480 392 555 330 C630 268 780 222 960 190 Z" fill="#ffffff"/>
      <path d="M365 410 C330 480 260 530 130 548 C270 540 340 490 365 410 Z" fill="var(--ink)"/>
    </svg>

    <div class="company">
      <div class="company__name">PEARLWOOD</div>
      <div class="company__tag">FRAMING WORKS</div>
    </div>

    <div class="brandmark">
      <span class="brandmark__square"></span>
      <span>PEARLWOOD<br>PLUMBING WORKS</span>
    </div>

    <div class="person">
      <div class="person__name">Employee Name</div>
      <div class="person__role">Managing Director</div>
    </div>

    <ul class="contact">
      <li class="contact__item">(512)555-0193
        <svg class="contact__icon" viewBox="0 0 24 24"><circle cx="12" cy="7" r="5"/><path d="M3 23c0-6 4-9 9-9s9 3 9 9z"/></svg>
      </li>
      <li class="contact__item">pearlwoodframingworks@mailnest.example
        <svg class="contact__icon" viewBox="0 0 24 24"><path d="M2 5h20v14H2z"/><path d="M2 5l10 8 10-8" fill="none" stroke="#1c1a63" stroke-width="2"/></svg>
      </li>
      <li class="contact__item">7732 Fernglen Pass LN Austin, TX 78734
        <svg class="contact__icon" viewBox="0 0 24 24"><path d="M12 2L1 12h3v10h6v-6h4v6h6V12h3z"/></svg>
      </li>
    </ul>
  </div>
</body>
</html>
```